Healthy lifestyle Influencer business card

I need your creativity to have a business card that I can leave in all the restaurants, hotels and spas I visit to inform them that I am an influencer specializing in the wellness sector and that I will write a review about them. You can use my instagram photos Lunavita27 or on my website www.piattileggeriorto.it. I would like my business card to impress with its creativity! thank you very much!

Contact Information for Business Card

siteweb, instagram, phone number

Font styles to use
Decorative
Script

Colors
0094D4
00A9DD
6FCCEA
C7EBF8
E9F6FB
59FF00
82FF00
B8FF75
E3FFCB
F4FFEA
FFC000
F8CF3A
FAE287
FDF2CF
FEFAEE
F0912C
F2A743
F7CA91
FBE8D2
FDF5EE
EE7325
F08F49
F5BC92
FAE3D3
FDF4ED
EB3D1F
EC4F4E
F09395
F8D3D4
FCEDEE
E54698
E96AAD
F1A4CE
F9D9EA
FCEFF6

Requirements
Nice to have
• creativity

```html
<!DOCTYPE html>
<html lang="it">
<head>
<meta charset="utf-8">
<title>Luna Vita Chef – Biglietto da visita</title>
<link rel="stylesheet" href="https://fonts.googleapis.com/css2?family=Quicksand:wght@400;500;600&display=swap">
<style>
  :root {
    --bg: #e9e7ea;
    --violet: #e786e3;
    --pink: #f39fc8;
    --peach: #fbb597;
    --white: #ffffff;
    --white-soft: rgba(255,255,255,0.28);
    --bubble: rgba(226,190,240,0.55);
    --icon: #f0a0c8;
    --photo-a: #8fa86a;
    --photo-b: #d9c7b4;
    --photo-c: #a9cfc9;
  }
  * { box-sizing: border-box; margin: 0; padding: 0; }
  html, body { width: 1200px; height: 873px; overflow: hidden; }
  body {
    background: var(--bg);
    font-family: "Quicksand", sans-serif;
    display: flex;
    align-items: center;
    justify-content: center;
    gap: 44px;
  }
  .card {
    position: relative;
    width: 540px;
    height: 309px;
    border-radius: 4px;
    overflow: hidden;
    color: var(--white);
    box-shadow: 0 10px 28px rgba(60,40,70,0.18);
  }
  .brand-name { font-size: 28px; font-weight: 500; letter-spacing: 0.5px; line-height: 1; white-space: nowrap; }
  .brand-tagline { font-size: 11px; font-weight: 600; margin-top: 7px; letter-spacing: 0.3px; white-space: nowrap; }

  /* Back side: contact details */
  .card--back {
    background: linear-gradient(100deg, var(--violet) 0%, var(--pink) 45%, var(--peach) 100%);
  }
  .card--back .divider {
    position: absolute; top: 0; bottom: 0; left: 128px;
    width: 1.5px; background: var(--white);
  }
  .card--back .icon-band {
    position: absolute; left: 22px; top: 18px; width: 84px; height: 273px;
    border-radius: 42px;
    background: var(--white-soft);
  }
  .card--back .bubble { position: absolute; border-radius: 50%; background: var(--bubble); }
  .card--back .bubble--a { right: 22px; top: 14px; width: 64px; height: 64px; }
  .card--back .bubble--b { right: 118px; bottom: 18px; width: 48px; height: 48px; }
  .card--back .brand { position: absolute; left: 162px; top: 44px; }
  .card--back .moon-area {
    position: absolute; right: 20px; bottom: 20px; width: 70px; height: 70px;
    border-radius: 50%; background: var(--white-soft);
  }
  .contacts {
    position: absolute; left: 160px; top: 132px;
    list-style: none; display: flex; flex-direction: column; gap: 14px;
  }
  .contacts li {
    display: flex; align-items: center; gap: 14px;
    font-size: 22px; font-weight: 400; letter-spacing: 0.4px; line-height: 28px; white-space: nowrap;
  }
  .contacts .dot {
    width: 18px; height: 18px; border-radius: 50%; background: var(--white);
    display: flex; align-items: center; justify-content: center; flex: none;
  }
  .contacts .dot svg { width: 12px; height: 12px; }

  /* Front side: portrait and brand */
  .card--front {
    background: linear-gradient(30deg, var(--peach) 0%, var(--pink) 50%, var(--violet) 100%);
  }
  .frame-line { position: absolute; background: var(--white); }
  .frame-line--top { left: 0; right: 0; top: 22px; height: 1.5px; }
  .frame-line--bottom { left: 0; right: 0; bottom: 22px; height: 1.5px; }
  .frame-line--left { top: 0; bottom: 0; left: 30px; width: 1.5px; }
  .frame-line--right { top: 0; bottom: 0; right: 30px; width: 1.5px; }
  .portrait {
    position: absolute; left: 58px; top: 50px; width: 250px; height: 230px;
    border-radius: 0 115px 115px 0;
    background: linear-gradient(160deg, var(--photo-a) 0%, var(--photo-b) 55%, var(--photo-c) 100%);
  }
  .card--front .brand { position: absolute; right: 48px; top: 62px; text-align: right; }
  .card--front .deco-area {
    position: absolute; right: 60px; bottom: 40px; width: 90px; height: 90px;
    border-radius: 50%; background: var(--white-soft);
  }
</style>
</head>
<body>

  <section class="card card--back" aria-label="Retro del biglietto">
    <div class="icon-band" role="img" aria-label="Fascia di icone decorative di cibo"></div>
    <div class="divider"></div>
    <div class="bubble bubble--a"></div>
    <div class="bubble bubble--b"></div>
    <div class="brand">
      <p class="brand-name">Luna Vita Chef</p>
      <p class="brand-tagline">Leggera e felice a ogni morso</p>
    </div>
    <ul class="contacts">
      <li>
        <span class="dot">
          <svg viewBox="0 0 24 24"><path fill="var(--icon)" d="M6.6 10.8a15 15 0 0 0 6.6 6.6l2.2-2.2c.3-.3.7-.4 1-.2 1.1.4 2.3.6 3.6.6.6 0 1 .4 1 1V20c0 .6-.4 1-1 1A17 17 0 0 1 3 4c0-.6.4-1 1-1h3.5c.6 0 1 .4 1 1 0 1.3.2 2.5.6 3.6.1.3 0 .7-.2 1z"/></svg>
        </span>
        008 412 735 9021
      </li>
      <li>
        <span class="dot">
          <svg viewBox="0 0 24 24" fill="none" stroke="var(--icon)" stroke-width="2"><circle cx="12" cy="12" r="9"/><path d="M3 12h18M12 3c3 3 3 15 0 18M12 3c-3 3-3 15 0 18"/></svg>
        </span>
        www.piattileggeriorto.it
      </li>
      <li><span class="dot"></span>@Lunavita27</li>
    </ul>
    <div class="moon-area" role="img" aria-label="Ornamento a forma di luna"></div>
  </section>

  <section class="card card--front" aria-label="Fronte del biglietto">
    <div class="frame-line frame-line--top"></div>
    <div class="frame-line frame-line--bottom"></div>
    <div class="frame-line frame-line--left"></div>
    <div class="frame-line frame-line--right"></div>
    <div class="portrait" role="img" aria-label="Foto ritratto della influencer all'aperto tra il verde vicino al mare"></div>
    <div class="brand">
      <p class="brand-name">Luna Vita Chef</p>
      <p class="brand-tagline">Leggera e felice a ogni morso</p>
    </div>
    <div class="deco-area" role="img" aria-label="Ornamento floreale decorativo"></div>
  </section>

</body>
</html>
```